Business card design for a teacher - double sided, sleek design.

My name is Lina and I am an online Arabic language teacher. I am looking for a beautiful business card design for my online teaching business.

The cards will be printed in 85mm x 55mm size.
The card can be either portrait or landscape.

The design should contain my logo on one side and information on the other.

The design needs to be clean and modern. Use of subtle Arabic geometric patterns would be nice. Icons for the social media information on the card should also match the design theme.

My logo font is Consolas, which is a Monospace font.

Business card design should be delivered with editable PSD or EPS files in the handover.

Thanks

Lina

----

Information on the back:

URL: www.speakwithnadia.net [this should stand out more than other details]
Email: info@speakwithnadia.net
Instagram: @speakwithnadia
Facebook: facebook.com/speakwithnadia
Skype: speakwithnadia

My brand colours are shown in the logo attached. These are:
- Teal green - 4DC9C1
- Mango yellow - FFD600

Target Market(s)

- Young professionals
- Expatriates
- Women and Men

Industry/Entity Type

Education

Contact Information for Business Card

Information on the back:

Skype: speakwithnadia

- Teal green - 4DC9C1
- Mango yellow - FFD600

Font styles to use
Other font styles liked:
• Any font complimentary to my logo font which is a Monospace font called Consolas.

Colors

Designer to choose colors to be used in the design.

Requirements
Must have
• - Aesthetically pleasing look
• - Complimentary design with existing logo
Nice to have
• Arabic geometrical patterns

```html
<!DOCTYPE html>
<html lang="en">
<head>
<meta charset="utf-8">
<title>Arabic with Lina – Business Card</title>
<link rel="stylesheet" href="https://fonts.googleapis.com/css2?family=Source+Sans+3:wght@400&display=swap">
<style>
  :root {
    --stage: #474745;
    --teal: #4dc9c1;
    --teal-deep: #48c2ba;
    --mango: #ffd600;
    --paper-light: #fafafa;
    --paper-edge: #e4e4e4;
    --ink: #555555;
    --rule: #9a9a9a;
    --white: #ffffff;
  }
  * { margin: 0; padding: 0; box-sizing: border-box; }
  html, body {
    width: 1200px; height: 960px; overflow: hidden;
    background: var(--stage);
  }
  .card {
    position: absolute;
    left: 312px; width: 600px; height: 344px;
    border-radius: 20px; overflow: hidden;
  }
  .card--front {
    top: 103px;
    background: radial-gradient(ellipse at 50% 55%, var(--paper-light) 0%, #f0f0f0 55%, var(--paper-edge) 100%);
  }
  .card--back { top: 500px; background: var(--teal); }

  .front-bands { position: absolute; inset: 0; }

  .brand {
    position: absolute; left: 60px; top: 160px;
    display: flex; align-items: center; gap: 10px;
    font-family: "Source Sans 3", sans-serif; font-weight: 400;
    font-size: 23px; line-height: 1; color: var(--ink);
    white-space: nowrap;
  }
  .brand__dot {
    width: 14px; height: 14px; background: var(--teal); flex: none;
  }

  .divider {
    position: absolute; left: 295px; top: 102px;
    width: 1px; height: 136px; background: var(--rule);
  }

  .contacts {
    position: absolute; left: 313px; top: 114px;
    list-style: none;
    font-family: "Source Sans 3", sans-serif; font-size: 16.5px;
    color: var(--ink);
  }
  .contacts li { display: flex; align-items: center; height: 23px; white-space: nowrap; }
  .contacts svg { width: 14px; height: 14px; margin-right: 7px; flex: none; }

  .pattern-field { position: absolute; inset: 0; background: linear-gradient(var(--teal), var(--teal-deep)); }

  .back-name {
    position: absolute; left: 0; right: 0; top: 145px;
    text-align: center;
    font-family: "Source Sans 3", sans-serif; font-weight: 400;
    font-size: 36px; line-height: 1; color: var(--white);
  }
  .back-url {
    position: absolute; left: 0; right: 0; top: 293px;
    text-align: center;
    font-family: "Source Sans 3", sans-serif; font-size: 15px;
    letter-spacing: 4.6px; color: var(--white);
  }
</style>
</head>
<body>
  <section class="card card--front">
    <svg class="front-bands" width="600" height="344" viewBox="0 0 600 344">
      <polygon points="0,0 582,0 0,54" fill="var(--mango)"/>
      <polygon points="0,344 600,290 600,344" fill="var(--teal)"/>
    </svg>

    <div class="brand">
      <span class="brand__dot"></span>
      <span>Arabic with Lina</span>
    </div>

    <div class="divider"></div>

    <ul class="contacts">
      <li>
        <svg viewBox="0 0 14 14"><rect x="1" y="3" width="12" height="8" fill="none" stroke="var(--teal)" stroke-width="1.4"/><polyline points="1,3 7,8 13,3" fill="none" stroke="var(--teal)" stroke-width="1.4"/></svg>
        info@speakwithnadia.net
      </li>
      <li>
        <svg viewBox="0 0 14 14"><rect x="1" y="1" width="12" height="12" rx="2" fill="var(--teal)"/></svg>
        @speakwithnadia
      </li>
      <li>
        <svg viewBox="0 0 14 14"><rect x="1" y="1" width="12" height="12" rx="2" fill="var(--teal)"/></svg>
        speakwithnadia
      </li>
      <li>
        <svg viewBox="0 0 14 14"><rect x="1" y="1" width="12" height="12" rx="2" fill="var(--teal)"/></svg>
        speakwithnadia
      </li>
      <li>
        <svg viewBox="0 0 14 14"><circle cx="7" cy="7" r="6" fill="var(--teal)"/><ellipse cx="7" cy="7" rx="2.6" ry="6" fill="none" stroke="var(--white)" stroke-width="1"/><line x1="1" y1="7" x2="13" y2="7" stroke="var(--white)" stroke-width="1"/></svg>
        speakwithnadia.net
      </li>
    </ul>
  </section>

  <section class="card card--back">
    <div class="pattern-field" role="img" aria-label="Subtle repeating tile pattern in lighter teal tones"></div>
    <p class="back-name">Arabic with Lina</p>
    <p class="back-url">WWW.SPEAKWITHNADIA.NET</p>
  </section>
</body>
</html>
```